Private Investment Firm Needs PowerPoint Presentation Template

Design PowerPoint template, take Pinebrook-submitted rough presentation draft, and drop it into new template. See attached Project Brief file for more detail.
Updates

Some decent designs have been submitted but they seem to lack the understanding of our target markets. I am hopeful that more time and feedback will result in better results.

Target Market(s)

Private company owners and intermediaries.

Font styles to use
Serif

Colors
3176b5

Requirements
Must have
• See attached Project Brief.
Nice to have
Should not have
• No B2C fluff--this is a B2B project.

```html
<!DOCTYPE html>
<html lang="en">
<head>
<meta charset="utf-8">
<title>The 12 Primary Uses of Non-Control Capital</title>
<link rel="stylesheet" href="https://fonts.googleapis.com/css2?family=Montserrat:wght@500;600;700&family=Tinos&display=swap">
<style>
  :root {
    --brand-blue: #0b6fbf;
    --side-blue: #1670c4;
    --navy: #264a6b;
    --mid-blue: #0a6ebd;
    --light-blue: #4a91c9;
    --card-bg: #f2f2f2;
    --card-border: #dcdcdc;
    --text: #222;
    --white: #fff;
  }
  * { margin: 0; padding: 0; box-sizing: border-box; }
  html, body { width: 1200px; height: 676px; overflow: hidden; background: var(--white); }
  .slide {
    position: relative; width: 1200px; height: 676px; overflow: hidden;
    font-family: "Montserrat", Arial, sans-serif; color: var(--text);
  }
  .side-band { position: absolute; left: 0; top: 0; width: 44px; height: 676px; background: var(--side-blue); }
  .edge-band { position: absolute; right: 0; top: 0; width: 11px; height: 676px; background: var(--side-blue); }
  .side-url {
    position: absolute; left: 22px; top: 336px;
    transform: translate(-50%, -50%) rotate(-90deg);
    font-family: "Tinos", "Times New Roman", serif; font-size: 16px;
    color: var(--white); white-space: nowrap;
  }
  .page-number {
    position: absolute; right: 46px; top: 18px;
    font-family: "Tinos", "Times New Roman", serif; font-size: 18px; color: #333;
  }
  .slide-title {
    position: absolute; left: 44px; right: 11px; top: 78px; text-align: center;
    font-weight: 700; font-size: 31px; letter-spacing: 0.3px; color: var(--brand-blue);
  }
  .uses-grid {
    position: absolute; left: 156px; top: 150px;
    display: grid; grid-template-columns: repeat(4, 224px);
    grid-template-rows: repeat(3, 132px); column-gap: 13px; row-gap: 18px;
  }
  .use-card {
    background: var(--card-bg); border: 1px solid var(--card-border);
    border-radius: 10px; display: flex; flex-direction: column; align-items: center;
    box-shadow: 0 1px 3px rgba(0,0,0,0.08);
  }
  .use-title {
    width: 189px; min-height: 38px; padding: 4px 6px;
    border-radius: 0 0 4px 4px; color: var(--white);
    font-weight: 500; font-size: 15px; line-height: 14.5px; text-align: center;
    display: flex; align-items: center; justify-content: center;
  }
  .row-navy .use-title { background: var(--navy); }
  .row-mid .use-title { background: var(--mid-blue); }
  .row-light .use-title { background: var(--light-blue); }
  .use-text {
    flex: 1; display: flex; align-items: center; padding: 6px 12px;
    font-size: 9.2px; line-height: 14.4px; text-align: center; font-weight: 500;
  }
  .brand {
    position: absolute; left: 68px; top: 615px;
    display: flex; align-items: center; gap: 10px;
  }
  .brand-dot { width: 36px; height: 36px; border-radius: 50%; background: var(--brand-blue); }
  .brand-name { font-weight: 600; font-size: 17px; color: var(--navy); letter-spacing: 1px; }
</style>
</head>
<body>
<div class="slide">
  <div class="side-band"></div>
  <div class="edge-band"></div>
  <div class="side-url">www.pinebrookcapital.com</div>
  <div class="page-number">5</div>

  <h1 class="slide-title">THE 12 PRIMARY USES OF NON-CONTROL CAPITAL</h1>

  <div class="uses-grid">
    <div class="use-card row-navy">
      <div class="use-title">Growth</div>
      <p class="use-text">Capital used to organically expand a business: introduce new products, build a new factory, hire additional management or employees, enter new markets, or for general working capital purposes</p>
    </div>
    <div class="use-card row-navy">
      <div class="use-title">Acquisitions</div>
      <p class="use-text">Capital used to acquire one or more competitors or to allow for further vertical or horizontal integration</p>
    </div>
    <div class="use-card row-navy">
      <div class="use-title">Partner or Shareholder Buy-Out</div>
      <p class="use-text">Capital used to buy-out an inactive or retiring partner or shareholder.</p>
    </div>
    <div class="use-card row-navy">
      <div class="use-title">Management Buy-Out (MBO)</div>
      <p class="use-text">When the incumbent management team buys most or all of the ownership of an inactive founder or executive</p>
    </div>

    <div class="use-card row-mid">
      <div class="use-title">Management Buy-In (MBI)</div>
      <p class="use-text">When an external, experienced executive buys a business from one or more inactive owners and needs additional capital to affect the purchase</p>
    </div>
    <div class="use-card row-mid">
      <div class="use-title">Family Ownership &amp; Wealth Transfer</div>
      <p class="use-text">When junior generations of a family acquire most or all of the ownership interests of more senior generations allowing the business to remain in the family name</p>
    </div>
    <div class="use-card row-mid">
      <div class="use-title">Balance Sheet Recapitalization</div>
      <p class="use-text">Changes the debt and equity mixture of a Company's finances to a more optimal capital structure</p>
    </div>
    <div class="use-card row-mid">
      <div class="use-title">Refinancing</div>
      <p class="use-text">Replacing one form or type of debt with another with better terms, conditions, and flexibility</p>
    </div>

    <div class="use-card row-light">
      <div class="use-title">Family Office Support</div>
      <p class="use-text">Allows a Family Office to affect an investment in a Company by allowing a junior capital provider to invest alongside them</p>
    </div>
    <div class="use-card row-light">
      <div class="use-title">Senior Lender Enhancement or Transition</div>
      <p class="use-text">When a Company has grown beyond the means or interest of its senior bank but needs additional capital to support its continuing growth</p>
    </div>
    <div class="use-card row-light">
      <div class="use-title">De-Lever Balance Sheet</div>
      <p class="use-text">When a Company has taken on too much debt (typically senior debt) and replaces some of it with either equity or other junior capital to provide operating flexibility</p>
    </div>
    <div class="use-card row-light">
      <div class="use-title">Owner Dividend (Liquidity)</div>
      <p class="use-text">When one or more owners take a non-life changing cash distribution, typically used to diversify their net worth</p>
    </div>
  </div>

  <div class="brand">
    <span class="brand-dot"></span>
    <span class="brand-name">PINEBROOK CAPITAL</span>
  </div>
</div>
</body>
</html>
```